Bright Towns Forum PowerPoint Design Template and Sample Deck

The Bright Towns Forum is an international organization that seeks to improve the livability, workability and sustainability of the world’s cities.
We seek a versatile PowerPoint design template with 10 slide types plus a “self-documenting” sample deck. Your design will be used in keynote speeches and workshops around the world.
After the contest is completed, we will ask the winning designer to add 10-20 additional slide types for $75 per slide. We also seek a long-term relationship whereby we can request “custom” slides and/or ask the designer to touch up the slides we build to make them better.
FILES. We have uploaded several files:
2. PALETTE. Shows our official colors.
3 LOGOS. Several individual files with different variations of our logo. Some with our motto, some without.
2. SAMPLE SLIDES. Because we were unable to successfully upload our sample deck, we are making it available via this FileNook link:
https://www.filenook-example.com/s/k7qrtmzp2wd9hxa/The%20Bright%20Towns%20Forum%20Design%20Contest%20Notes.docx?dl=0
Target Market(s)
Mayors, department heads, CIOs, senior executives from technology companies
Industry/Entity Type
Information Technology
Colors
Designer to choose colors to be used in the design.
Requirements
Must have
- Please see uploaded Word document for requirements, nice to haves and should not haves and uploaded palette for color preferences.
Nice to have
- see above
Should not have
- see above

```html
<!DOCTYPE html>
<html lang="en">
<head>
<meta charset="utf-8">
<title>Bright Towns Forum – Slide Template Overview</title>
<link href="https://fonts.googleapis.com/css2?family=Open+Sans:ital,wght@0,400;0,600;0,700;1,400;1,600&display=swap" rel="stylesheet">
<style>
:root{
  --navy:#0d2d5a;
  --navy-soft:#1f416f;
  --orange:#f7941d;
  --orange-deep:#e07b10;
  --red-orange:#f15a29;
  --green:#7a9a2a;
  --ink:#1c1c1c;
  --white:#ffffff;
}
*{box-sizing:border-box;margin:0;padding:0}
html,body{width:1200px;height:1151px;overflow:hidden;background:#fff}
body{font-family:"Open Sans",Arial,sans-serif;color:var(--ink);position:relative}
.slide{position:absolute;width:393px;height:219px;overflow:hidden;background:var(--white)}
.c1{left:3px}.c2{left:403px}.c3{left:803px}
.r1{top:0}.r2{top:227px}.r3{top:455px}.r4{top:683px}.r5{top:912px}
.abs{position:absolute}
.o{color:var(--orange)}
.n{color:var(--navy)}
.footer{position:absolute;left:0;right:0;bottom:0;height:10px;background:var(--navy);color:#fff;font-size:4.5px;display:flex;align-items:center;justify-content:space-between;padding:0 0 0 12px}
.footer .copy{margin-left:auto;margin-right:8px}
.footer .num{width:18px;height:10px;background:var(--orange);display:flex;align-items:center;justify-content:center;font-size:4.5px}
.title{position:absolute;left:0;top:6px;padding-left:12px;border-left:4px solid var(--orange);font-weight:600;font-size:17px;color:var(--navy);line-height:1.2}
.photo{position:absolute}
.enh-label{position:absolute;font-size:11.5px;font-weight:600;line-height:1.35;white-space:nowrap}
</style>
</head>
<body>

<!-- Row 1 -->
<section class="slide c1 r1">
  <div class="abs" style="left:0;top:0;width:393px;height:118px;background:var(--navy)"></div>
  <div class="abs" style="left:86px;top:26px;color:#fff;font-size:22px;line-height:.95">Bright<br>Towns<br>Forum</div>
  <div class="abs" style="left:196px;top:35px;width:1px;height:56px;background:#8797b0"></div>
  <div class="abs" style="left:225px;top:36px;color:#fff;font-size:11.5px;line-height:1.65">Liveability<br>Workability<br>Sustainability</div>
  <div class="abs" style="left:0;top:128px;width:393px;text-align:center;font-weight:700;font-size:19px;line-height:1.17;color:var(--navy)">This Is The Implementation of the<br><span class="o">Template in your current<br>Presentation</span></div>
</section>

<section class="slide c2 r1">
  <div class="abs" style="left:0;top:0;width:393px;height:127px;background:var(--navy)"></div>
  <div class="abs" style="left:0;top:34px;width:393px;text-align:center;color:#fff;font-weight:600;font-size:23px">The world is <span class="o" style="font-size:26px">changing</span></div>
  <div class="abs" style="left:0;top:76px;width:393px;text-align:center;color:#fff;font-size:8px;line-height:1.45">“The biggest shift in economic gravity in history.”<br><i>&nbsp;&nbsp;- Harlow &amp; Finch -</i></div>
  <div class="abs" style="left:19px;top:159px;color:var(--navy);font-size:19px">Bright Towns Forum</div>
  <div class="abs" style="left:20px;top:181px;color:var(--navy);font-size:5.5px;letter-spacing:1.4px">LIVABILITY | WORKABILITY | SUSTAINABILITY</div>
  <div class="abs" style="right:10px;top:170px;color:var(--navy);font-size:7px;font-weight:700">www.brighttownsforum.example</div>
</section>

<section class="slide c3 r1" style="background:var(--navy)">
  <div class="abs" style="left:10px;top:74px;border-left:4px solid var(--orange);padding-left:5px;font-weight:600;font-size:16px;line-height:1.2;color:#fff">Cities Are<br><span class="o">Transforming</span></div>
  <div class="photo" role="img" aria-label="Monarch butterflies emerging from chrysalises on a branch" style="left:157px;top:0;width:236px;height:219px;background:linear-gradient(160deg,#8c8a76 0%,#b3ae92 40%,#c47b2a 75%,#6b5a3c 100%)"></div>
</section>

<!-- Row 2 -->
<section class="slide c1 r2">
  <div class="title" style="top:7px">Smart cities <span class="o">market size</span></div>
  <div class="abs" style="left:0;top:60px;width:196px;text-align:center;font-size:7px;line-height:1.4">
    <div class="o" style="font-size:13px;font-weight:600">$757 Billion</div><b>by 2020</b><br><span class="o">•</span>19% CAGR (compound annual growth rate)<br><span class="o">•</span>Trendline Research</div>
  <div class="abs" style="left:196px;top:60px;width:196px;text-align:center;font-size:7px;line-height:1.4">
    <div class="o" style="font-size:13px;font-weight:600">$1.38 Trillion</div><b>by 2020</b><br><span class="o">•</span>20% CAGR overall, 38% CAGR Asia-Pacific<br><span class="o">•</span>Vantage Insight</div>
  <div class="abs" style="left:0;top:138px;width:196px;text-align:center;font-size:7px;line-height:1.4">
    <div class="o" style="font-size:13px;font-weight:600">$1.45 Trillion</div><b>by 2020</b><br><span class="o">•</span>Quanta Metrics</div>
  <div class="abs" style="left:196px;top:138px;width:196px;text-align:center;font-size:7px;line-height:1.4">
    <div class="o" style="font-size:13px;font-weight:600">$41 Trillion</div><b>by 2020</b><br><span class="o">•</span>Cumulative spend over 20 years<br><span class="o">•</span>Civic Tech Institute</div>
  <div class="footer"><span>Bright Towns Forum</span><span class="copy">© 2017 Bright Towns Forum. All rights reserved.</span><span class="num">46</span></div>
</section>

<section class="slide c2 r2">
  <div class="photo" role="img" aria-label="Sepia photo of sprinters launching from starting blocks" style="inset:0;background:linear-gradient(120deg,#e9e5df 0%,#c9c3ba 45%,#6b655e 75%,#3a3632 100%)"></div>
  <div class="abs" style="left:20px;top:0;width:157px;height:95px;background:var(--navy-soft)"></div>
  <div class="abs" style="left:28px;top:30px;border-left:4px solid var(--orange);padding-left:7px;color:#fff;font-weight:600;font-size:13.5px;line-height:1.3">It’s not just a<br>trend, it’s a <span class="o" style="font-size:19px">race</span></div>
</section>

<section class="slide c3 r2">
  <div class="photo" role="img" aria-label="Black and white photo of a child wearing a breathing mask" style="inset:0;background:linear-gradient(135deg,#2a2a2a 0%,#6e6e6e 40%,#b5b5b5 70%,#8a8a8a 100%)"></div>
  <div class="abs" style="right:0;top:20px;width:148px;height:70px;background:var(--navy-soft)"></div>
  <div class="abs" style="right:10px;top:28px;border-right:4px solid var(--orange);padding-right:7px;text-align:right;color:#fff;font-weight:600;font-size:13.5px;line-height:1.2">A Race For<br><span class="o" style="font-size:15.5px">Environmental</span><br>Improvements</div>
  <div class="abs" style="left:10px;top:135px;width:178px;height:77px;background:var(--navy-soft);color:#fff;text-align:center;font-size:8.5px;line-height:1.6;padding-top:12px">The world’s largest cities have pollution<br><span class="o" style="font-size:12.5px;font-weight:600">2-8 times above</span> GHA<br>guidelines</div>
</section>

<!-- Row 3 -->
<section class="slide c1 r3" style="background:var(--orange)">
  <div class="abs" style="left:0;top:52px;width:393px;text-align:center;color:#fff;font-size:19px;line-height:1.2">There will be<br><span class="n" style="font-size:26px;font-weight:600">winners</span><br>and<br><span class="n" style="font-size:20px;font-weight:600">losers</span></div>
  <div class="photo" role="img" aria-label="Stylised city skyline silhouette" style="left:0;bottom:0;width:393px;height:50px;background:linear-gradient(180deg,var(--orange) 0%,var(--orange-deep) 55%,#c96e10 100%)"></div>
</section>

<section class="slide c2 r3">
  <div class="title" style="top:6px">Some cities are already <span class="o">pulling ahead…</span></div>
  <div class="photo" role="img" aria-label="Dubai skyline photo" style="left:0;top:47px;width:131px;height:110px;background:linear-gradient(180deg,#8fb3d6,#c9a27a)"></div>
  <div class="photo" role="img" aria-label="Singapore skyline photo" style="left:131px;top:47px;width:131px;height:110px;background:linear-gradient(180deg,#aec6d8,#4f6f58)"></div>
  <div class="photo" role="img" aria-label="New York street photo" style="left:262px;top:47px;width:131px;height:110px;background:linear-gradient(180deg,#9fb4c9,#6b5e58)"></div>
  <div class="abs" style="left:0;top:157px;width:131px;height:32px;background:var(--navy);color:#fff;text-align:center;font-size:8px;line-height:1.35;padding-top:5px"><b>Dubai</b><br>“Smartest city on earth”</div>
  <div class="abs" style="left:131px;top:157px;width:131px;height:32px;background:var(--orange);color:#fff;text-align:center;font-size:8px;line-height:1.35;padding-top:5px"><b>Singapore</b><br>“Smart nation”</div>
  <div class="abs" style="left:262px;top:157px;width:131px;height:32px;background:var(--navy);color:#fff;text-align:center;font-size:8px;line-height:1.35;padding-top:5px"><b>New York</b><br>OneCity</div>
  <div class="footer"><span>Bright Towns Forum</span><span class="copy">© 2017 Bright Towns Forum. All rights reserved.</span><span class="num">50</span></div>
</section>

<section class="slide c3 r3">
  <div class="photo" role="img" aria-label="Photo of an excited young girl shouting with joy" style="inset:0;background:linear-gradient(100deg,#6b3a22 0%,#c98c66 35%,#e4d6ce 65%,#f3f1ef 100%)"></div>
  <div class="abs" style="left:0;top:6px;border-left:4px solid var(--orange);padding-left:8px;color:#fff;font-weight:600;font-size:16px">Happier for Less</div>
  <div class="abs" style="left:285px;top:118px;font-size:11.5px;line-height:1.3;color:var(--ink)">Spend <i class="o">less</i> to<br>improve life for<br>your citizens</div>
  <div class="footer"><span>Bright Towns Forum</span><span class="copy">© 2017 Bright Towns Forum. All rights reserved.</span><span class="num">51</span></div>
</section>

<!-- Row 4 -->
<section class="slide c1 r4">
  <div class="abs" style="right:0;top:0;width:132px;height:219px;background:var(--navy)"></div>
  <div class="abs" style="left:0;top:6px;border-left:4px solid var(--orange);padding-left:8px;font-weight:600;font-size:16px;color:var(--navy)"><span class="o">Happier</span> for less</div>
  <div class="photo" role="img" aria-label="Two tablets showing the CityNow services app" style="left:127px;top:30px;width:217px;height:168px;background:linear-gradient(135deg,#2b2b2b,#5a5f66 50%,#2b2b2b)"></div>
  <div class="abs" style="left:6px;top:88px;font-size:11.5px;line-height:1.4;text-align:right;width:108px;white-space:nowrap">CityNow<br>smartphone app<br><span class="o" style="font-weight:600">$1 billion saved</span></div>
  <div class="footer"><span>Bright Towns Forum</span><span class="copy">© 2017 Bright Towns Forum. All rights reserved.</span><span class="num">52</span></div>
</section>

<section class="slide c2 r4">
  <div class="photo" role="img" aria-label="Portrait photo of a speaker resting her chin on her hand" style="inset:0;background:linear-gradient(90deg,#e6e8ec 0%,#d9dde4 50%,#b79a86 75%,#8b8f9c 100%)"></div>
  <div class="abs" style="left:9px;top:57px;font-size:10.5px;line-height:1.4;color:var(--ink)">For Those Of Us Living In Cities, We<br>Need To Make Sure They Are Smart Cities.<br><span class="o" style="font-size:14px;font-weight:600">Nothing Else Makes Sense</span><br>And Nothing Else Is Such A World-wide<br><span class="o" style="font-size:14px;font-weight:600">Economic Opportunity</span></div>
  <div class="abs" style="left:9px;top:180px;font-size:7px;font-style:italic"><span class="o" style="font-size:11px;font-weight:600">Maren Vos</span>&nbsp;&nbsp; Vice President Regional Commission</div>
  <div class="footer"><span>Bright Towns Forum</span><span class="copy">© 2017 Bright Towns Forum. All rights reserved.</span><span class="num">54</span></div>
</section>

<section class="slide c3 r4" style="background:var(--navy)">
  <div class="abs" style="left:10px;top:76px;border-left:4px solid var(--orange);padding-left:6px;color:#fff;font-weight:600;font-size:15.5px;line-height:1.3">Free <span class="o">Smart City</span><br>Resources</div>
  <div class="photo" role="img" aria-label="Screenshot of the Forum website homepage with news and resources" style="left:163px;top:12px;width:212px;height:195px;background:linear-gradient(180deg,#ffffff 0%,#ffffff 15%,#dde3ec 40%,#f2f4f7 60%,#ffffff 100%);box-shadow:0 1px 4px rgba(0,0,0,.4)"></div>
</section>

<!-- Row 5 -->
<section class="slide c1 r5">
  <div class="photo" role="img" aria-label="Photo of a workshop audience seated in a conference hall" style="inset:0;background:linear-gradient(160deg,#4a4f5a 0%,#7a7c82 40%,#55504c 70%,#2d2f35 100%)"></div>
  <div class="abs" style="left:0;top:6px;border-left:4px solid var(--orange);padding-left:8px;color:#fff;font-weight:600;font-size:16px">Readiness <span class="o">Workshops</span></div>
  <div class="abs" style="left:228px;top:73px;width:165px;height:136px;background:rgba(31,65,111,.92);padding:22px 0 0 16px;color:#fff;font-size:11.5px;line-height:1.6">Readiness <span class="o">Workshops</span><br>Readiness <span class="o">Assessments</span><br>Readiness <span class="o">Plans</span><br>Smart city <span class="o">accelerators</span></div>
  <div class="footer"><span>Bright Towns Forum</span><span class="copy">© 2017 Bright Towns Forum. All rights reserved.</span><span class="num">55</span></div>
</section>

<section class="slide c2 r5">
  <div class="title" style="top:6px">2018 <span class="o">Enhancements</span></div>
  <svg class="abs" style="left:133px;top:45px" width="128" height="128" viewBox="0 0 128 128" aria-hidden="true">
    <g transform="rotate(-180 64 64)" fill="none" stroke-width="26">
      <circle cx="64" cy="64" r="49" stroke="var(--red-orange)" stroke-dasharray="73 235"/>
      <circle cx="64" cy="64" r="49" stroke="var(--navy)" stroke-dasharray="73 235" transform="rotate(90 64 64)"/>
      <circle cx="64" cy="64" r="49" stroke="var(--orange)" stroke-dasharray="73 235" transform="rotate(180 64 64)"/>
      <circle cx="64" cy="64" r="49" stroke="var(--navy)" stroke-dasharray="73 235" transform="rotate(270 64 64)"/>
    </g>
    <circle cx="64" cy="64" r="34" fill="#fff"/>
    <text x="64" y="70" text-anchor="middle" font-family="Open Sans, sans-serif" font-weight="600" font-size="16" fill="var(--navy)">2018</text>
    <circle cx="56" cy="21" r="9" fill="#fff"/>
    <circle cx="107" cy="56" r="9" fill="#fff"/>
    <circle cx="72" cy="107" r="9" fill="#fff"/>
    <circle cx="21" cy="72" r="9" fill="#fff"/>
  </svg>
  <div class="enh-label" style="right:277px;top:51px;text-align:right;color:var(--red-orange)">More time with<br>more cities</div>
  <div class="enh-label" style="left:278px;top:51px;color:var(--navy)">More help<br>for cities</div>
  <div class="enh-label" style="right:281px;top:151px;text-align:right;color:var(--navy)">More data<br>about cities</div>
  <div class="enh-label" style="left:276px;top:151px;color:var(--orange)">More visibility<br>for sponsors</div>
  <div class="footer"><span>Bright Towns Forum</span><span class="copy">© 2017 Bright Towns Forum. All rights reserved.</span><span class="num">56</span></div>
</section>

<section class="slide c3 r5">
  <div class="title" style="top:6px">Sponsorship <span class="o">Levels</span></div>
  <div class="abs" style="left:0;top:82px;width:393px;height:127px;background:var(--navy)"></div>
  <div class="abs" style="left:31px;top:37px;width:151px;height:164px;background:#fff;box-shadow:0 0 0 1px #ccd">
    <div style="height:44px;background:var(--orange);color:#fff;text-align:center;padding-top:8px;font-size:13px;line-height:1.05">$10,000<br><span style="font-size:7px">Supporting</span></div>
    <div style="font-size:6.8px;text-align:center;padding:4px 8px;line-height:1.2">
      <div style="padding:2px 0;border-bottom:1px solid #ccc">In-kind optional</div>
      <div style="padding:2px 0;border-bottom:1px solid #ccc">Access to full data from all entering cities</div>
      <div style="padding:2px 0;border-bottom:1px solid #ccc">Article and social blasts about the in-kind contribution</div>
      <div style="padding:2px 0;border-bottom:1px solid #ccc">Included in all releases, marketing materials, on-site banners</div>
      <div style="padding:2px 0">Guaranteed one representative to all events – workshops, announcements, receptions, mentoring sessions</div>
    </div>
  </div>
  <div class="abs" style="left:211px;top:37px;width:151px;height:164px;background:#fff;box-shadow:0 0 0 1px #ccd">
    <div style="height:44px;background:var(--green);color:#fff;text-align:center;padding-top:8px;font-size:13px;line-height:1.05">$25,000<br><span style="font-size:7px">Premier</span></div>
    <div style="font-size:6.8px;text-align:center;padding:6px 8px;line-height:1.2">
      <div style="padding:3px 0 6px;border-bottom:1px solid #ccc">In-kind optional</div>
      <div style="padding:6px 0;border-bottom:1px solid #ccc">All Supporting benefits</div>
      <div style="padding:4px 0;border-bottom:1px solid #ccc">Guaranteed two representatives to all events</div>
      <div style="padding:4px 0">Speaking opportunity at all events •Opening remarks, how-to presentation, case study, facilitate breakout, panelist</div>
    </div>
  </div>
  <div class="footer"><span>Bright Towns Forum</span><span class="copy">© 2017 Bright Towns Forum. All rights reserved.</span><span class="num">57</span></div>
</section>

</body>
</html>
```